Las Vegas Tour guide needs website of future for physical and selfguided assets

Neon Drifters is the parent site to my Las Vegas tour operation. Within this is a physical walking tour called Whispers and the Racket, the site traffic driver where I tell history with a paranormal twist. The legacy site can be seen at spookyroutewalks.com.
The Neon Drifters app has self guided tours called Desert Hop Trail/Whispers and The Racket Retold/Calloway Row Stroll. Rivano is a 3rd party tour company I have partnered with to sale self-guided tours with a scavenger hunt theme.
I like black and pink and pistachio green colors however am flexible in theme. Colors should follow Vegas 50-60s aesthetics. The “Greetings From Silver Gulch Marker” should not be considered as design inspiration. 95% of traffic is on mobile. Final design should be easy to understand guided versus self-guided option. Show cross promotion links for digital assets/physical tour. Rivano content tbd by end of week 9 Aug 2021
sites i like
nationalspiritstrolls.com
heronsandshades.com
oldportphantomtrips.net
Updates

Needs a book now at top, or floating like lorvantrips. Less busy and stay away from using photos. I have included more websites for inspiration. I would like a mashup of the two sites eerieechoplace and lorvantrips. I am unsure what some of your designs would look like on a mobile screen. Please screenshot that. https://eerieechoplace.com/ https://www.lorvantrips.com/ https://k7vrx.com/ https://bqspecters.com/ https://bluefinjaunts.com/tours/new-york-city/shades-of-pellham-corner/

Family member hospitalized need extra time to review

Target Market(s)

Tourist 25+

Industry/Entity Type

Travel. Tour guide.

Coding

Coded - Design and coding required

Number of Pages Required

5+ page

Font styles to use
Serif

Colors
00AB8E
00BBA5
67D7C9
C6EFE9
E9F9F6
59FF00
82FF00
B8FF75
E3FFCB
F4FFEA
EB3D1F
EC4F4E
F09395
F8D3D4
FCEDEE
E54698
E96AAD
F1A4CE
F9D9EA
FCEFF6

Requirements
Must have
• Cross promotion between physical tour and digital
Nice to have
• sliver button like ads as breaks between tour info
Should not have
• "Greetings from Silver Gulch Marker". no photos. no animation.

```html
<!DOCTYPE html>
<html lang="en">
<head>
<meta charset="utf-8">
<title>Calloway Row Stroll</title>
<link href="https://fonts.googleapis.com/css2?family=Cabin:wght@400;500;600;700&family=Lato:wght@400;700&family=Caveat:wght@400&display=swap" rel="stylesheet">
<style>
  :root {
    --pink: #e6149a;
    --pink-soft: #e96aad;
    --pink-deep: #b43aa0;
    --teal: #00ab8e;
    --teal-light: #67d7c9;
    --orange: #f0801e;
    --ink: #2b2b2b;
    --white: #ffffff;
    --black: #000000;
    --haze-top: #f3ede6;
    --haze-mid: #ece8e4;
    --haze-low: #e6e8ea;
  }
  * { box-sizing: border-box; margin: 0; padding: 0; }
  html, body { width: 1134px; height: 1200px; overflow: hidden; }
  body { position: relative; background: var(--white); font-family: "Lato", sans-serif; color: var(--ink); }

  .site-header { position: absolute; top: 0; left: 0; width: 1134px; height: 73px; background: var(--white); z-index: 3; }
  .brand-badge { position: absolute; left: 117px; top: -60px; width: 200px; height: 200px; border-radius: 50%; background: var(--white); z-index: 4; }
  .brand-badge .mark { position: absolute; left: 72px; top: 66px; width: 56px; height: 56px; border-radius: 50%; background: var(--orange); }
  .brand-badge .name { position: absolute; left: 0; width: 200px; top: 132px; text-align: center; font-family: "Cabin", sans-serif; font-weight: 700; font-size: 15px; color: var(--orange); }

  .main-nav { position: absolute; top: 29px; left: 426px; display: flex; gap: 27px; font-family: "Cabin", sans-serif; font-weight: 500; font-size: 12px; letter-spacing: .2px; }
  .main-nav a { color: var(--ink); text-decoration: none; }

  .call-box { position: absolute; left: 846px; top: 18px; }
  .call-icon { position: absolute; left: 0; top: 0; width: 38px; height: 38px; border-radius: 50%; background: var(--pink); }
  .call-icon svg { position: absolute; left: 11px; top: 11px; }
  .call-label { position: absolute; left: 48px; top: -6px; white-space: nowrap; font-family: "Caveat", cursive; font-size: 20px; color: var(--pink); }
  .call-number { position: absolute; left: 48px; top: 20px; white-space: nowrap; font-family: "Cabin", sans-serif; font-weight: 600; font-size: 17px; color: var(--ink); letter-spacing: .5px; }

  .hero { position: absolute; top: 73px; left: 0; width: 1134px; height: 731px; background: linear-gradient(180deg, var(--haze-top) 0%, var(--haze-mid) 55%, var(--haze-low) 100%); }

  .tour-card { position: absolute; left: 107px; top: 179px; width: 920px; height: 512px; background: var(--white); box-shadow: 0 4px 18px rgba(0,0,0,.12); }
  .tour-title { position: absolute; top: 36px; left: 0; width: 100%; text-align: center; font-family: "Cabin", sans-serif; font-weight: 600; font-size: 27px; color: var(--ink); letter-spacing: .3px; }

  .tour-options { position: absolute; top: 102px; left: 70px; width: 780px; height: 264px; display: flex; gap: 20px; }
  .tour-option { position: relative; flex: 1; border: 5px solid var(--white); box-shadow: 0 8px 14px rgba(0,0,0,.18); text-align: center; color: var(--white); }
  .option-guided { background: linear-gradient(160deg, #c45bc8 0%, #d152b0 45%, var(--pink-deep) 100%); }
  .option-self { background: linear-gradient(160deg, var(--teal-light) 0%, var(--teal) 100%); }
  .option-tag { position: absolute; top: 40px; left: 0; width: 100%; font-family: "Cabin", sans-serif; font-weight: 600; font-size: 12px; letter-spacing: 2px; }
  .option-name { position: absolute; top: 66px; left: 0; width: 100%; font-family: "Cabin", sans-serif; font-weight: 700; font-size: 22px; }
  .option-note { position: absolute; top: 106px; left: 30px; width: calc(100% - 60px); font-size: 13px; line-height: 20px; }
  .option-button { position: absolute; left: 50%; top: 176px; transform: translateX(-50%); width: 153px; height: 46px; border-radius: 23px; background: var(--white); font-family: "Cabin", sans-serif; font-weight: 500; font-size: 15px; display: flex; align-items: center; justify-content: center; }
  .option-guided .option-button { color: var(--pink); }
  .option-self .option-button { color: var(--teal); }

  .tour-summary { position: absolute; top: 394px; left: 0; width: 100%; text-align: center; font-size: 13px; line-height: 26.5px; color: var(--ink); }

  .site-footer { position: absolute; top: 804px; left: 0; width: 1134px; height: 396px; background: var(--black); color: var(--white); }
  .footer-brand { position: absolute; left: 467px; top: 32px; width: 200px; text-align: center; }
  .footer-brand .mark { display: block; margin: 0 auto; width: 68px; height: 68px; border-radius: 50%; background: var(--orange); }
  .footer-brand .name { display: block; margin-top: 14px; font-family: "Cabin", sans-serif; font-weight: 700; font-size: 18px; color: var(--orange); }
  .footer-nav { position: absolute; top: 171px; left: 0; width: 100%; display: flex; justify-content: center; gap: 27px; font-family: "Cabin", sans-serif; font-weight: 600; font-size: 12px; }
  .footer-nav a { color: var(--white); text-decoration: none; }
  .social-row { position: absolute; top: 206px; left: 0; width: 100%; display: flex; justify-content: center; gap: 13px; }
  .social-row span { width: 28px; height: 28px; border-radius: 50%; background: var(--white); }
  .store-row { position: absolute; top: 253px; left: 0; width: 100%; display: flex; justify-content: center; gap: 30px; }
  .store-row span { width: 144px; height: 42px; border: 1px solid #a6a6a6; border-radius: 7px; background: var(--black); }
  .copyright { position: absolute; top: 314px; left: 0; width: 100%; text-align: center; font-family: "Cabin", sans-serif; font-weight: 600; font-size: 11.5px; }
</style>
</head>
<body>
  <header class="site-header">
    <div class="brand-badge">
      <span class="mark"></span>
      <span class="name">Calloway Row Stroll</span>
    </div>
    <nav class="main-nav">
      <a href="#">HOME</a><a href="#">ABOUT US</a><a href="#">BLOGS</a><a href="#">CONTACT US</a>
    </nav>
    <div class="call-box">
      <span class="call-icon">
        <svg width="16" height="16" viewBox="0 0 24 24"><path fill="#fff" d="M6.6 10.8c1.4 2.8 3.8 5.1 6.6 6.6l2.2-2.2c.3-.3.7-.4 1-.2 1.1.4 2.3.6 3.6.6.6 0 1 .4 1 1V20c0 .6-.4 1-1 1C10.6 21 3 13.4 3 4c0-.6.4-1 1-1h3.5c.6 0 1 .4 1 1 0 1.3.2 2.5.6 3.6.1.3 0 .7-.2 1z"/></svg>
      </span>
      <span class="call-label">Call Us Today</span>
      <span class="call-number">(555) 014-2273</span>
    </div>
  </header>

  <section class="hero" role="img" aria-label="Faded skyline view of the city strip behind the tour card"></section>

  <main class="tour-card">
    <h1 class="tour-title">WHISPERS AND THE RACKET</h1>
    <div class="tour-options">
      <div class="tour-option option-guided">
        <span class="option-tag">GUIDED</span>
        <span class="option-name">Walking Tour</span>
        <p class="option-note">Walk with a live guide through three haunted properties</p>
        <span class="option-button">BOOK NOW</span>
      </div>
      <div class="tour-option option-self">
        <span class="option-tag">SELF-GUIDED</span>
        <span class="option-name">App Tours</span>
        <p class="option-note">Explore at your own pace with the Neon Drifters app</p>
        <span class="option-button">GET THE APP</span>
      </div>
    </div>
    <p class="tour-summary">
      Visit 3 haunted Las Vegas properties and hear the real stories that made them as they are<br>
      Highlights include the ghosts of mob bodyguards and stories from the Motel of Death!<br>
      Explore historic Downtown Las Vegas with an experienced guide on Calloway Row
    </p>
  </main>

  <footer class="site-footer">
    <div class="footer-brand">
      <span class="mark"></span>
      <span class="name">Calloway Row Stroll</span>
    </div>
    <nav class="footer-nav">
      <a href="#">HOME</a><a href="#">ABOUT US</a><a href="#">BLOGS</a><a href="#">CONTACT US</a>
    </nav>
    <div class="social-row"><span></span><span></span><span></span><span></span></div>
    <div class="store-row"><span></span><span></span></div>
    <p class="copyright">© Copyright 2021&nbsp; Stridetalk Co LLC &nbsp;|&nbsp;&nbsp; All Rights Reserved</p>
  </footer>
</body>
</html>
```